Cleaning Service Company In need of Good Web presence.

The company is a cleaning service company which provides professional staff and service for cleaning. This is a project to build a site that is both solid and a strong recognition of our organization. It is supposed to show quality, cleanliness, professionalism. The use of images and art for imagery is all good just to have a site that is consistent and solid. There might be a chance to make stationary, logo and business cars if someone feels they can build a brand that is consistent. The image we are going for is clean solid and to stand out. Finally stationary should not be expensive to print.

Current logo is attached and can be used or can be made more creative.

Target Market(s)

Corporate and Government entities, that will feel that this company has a brand that sets it apart from the rest. The company is new so the modification of the logo will not be an issue if a more solid brand come out of this project. The idea is to have a clean consistent product that stands our from others in terms of website, stationary, etc

Industry/Entity Type

Cleaning Service

Contact Information for Business Card

P.O.Box 51947
Riffa
Kingdom of Bahrain

Logo Text

Harbor Lane Services

Number of Pages Required

4 page

Font styles to use
Sans Serif

Colors
abd036
cadf82
eaf2ce
9bcb3b

Requirements
Must have
• Green Color to be used in order to stick to the name. Also the creativity and boldness in an elegant manner.
Nice to have
• Arabic name of company
• هاربر لين سرفسس ذ.م.م
• if cannot be put at least make a location should be chosen
• Also could be a bit of 3D given to the logo if it could stay elegent.
Should not have
• Should not show people cleaning.

```html
<!DOCTYPE html>
<html lang="en">
<head>
<meta charset="utf-8">
<title>Harbor Lane Services</title>
<link rel="stylesheet" href="https://fonts.googleapis.com/css2?family=Montserrat:wght@400;600;700&family=Open+Sans:wght@400;600&family=Noto+Naskh+Arabic:wght@500&display=swap">
<style>
:root{
  --green:#9bcb3b;
  --green-bright:#abd036;
  --green-soft:#cadf82;
  --green-pale:#eaf2ce;
  --green-deep:#0f6b3b;
  --ink:#222;
  --text:#555;
  --muted:#8a8a8a;
  --line:#e2e2e2;
  --grey-band:#ebebeb;
  --white:#fff;
}
*{box-sizing:border-box;margin:0;padding:0}
html,body{width:1200px;height:3237px;overflow:hidden;background:var(--white)}
body{position:relative;font-family:"Open Sans",Arial,sans-serif;color:var(--text)}
.abs{position:absolute}
.heading{font-family:"Montserrat",Arial,sans-serif}

/* header */
.site-header{position:absolute;left:0;top:0;width:1200px;height:125px;background:var(--white)}
.call{left:705px;top:26px;display:flex;align-items:center;gap:12px}
.call-icon{width:30px;height:30px;border-radius:50%;background:var(--green);display:flex;align-items:center;justify-content:center}
.call small{display:block;font:600 10px "Montserrat",sans-serif;color:var(--ink);letter-spacing:.5px}
.call strong{display:block;font:400 21px "Open Sans",sans-serif;color:var(--green)}
.quote-btn{left:930px;top:26px;width:136px;height:37px;background:var(--green-deep);color:var(--white);font:600 12px "Montserrat",sans-serif;display:flex;align-items:center;justify-content:center;gap:8px}
.main-nav{left:474px;top:87px;display:flex;font:600 11px "Montserrat",sans-serif;color:var(--ink);text-transform:uppercase}
.main-nav span{padding:5px 0;display:block}
.main-nav .active{background:var(--green);color:var(--white);padding:5px 11px}

.brand-badge{border-radius:50%;background:var(--white);display:flex;align-items:center;justify-content:center;text-align:center}
.brand-badge span{font:700 25px/1.15 "Montserrat",sans-serif;color:var(--green-deep);text-transform:uppercase;width:70%}
.header-badge{left:134px;top:-6px;width:234px;height:234px;box-shadow:0 2px 8px rgba(0,0,0,.12);z-index:3}

/* hero */
.hero{left:0;top:125px;width:1200px;height:600px;background:linear-gradient(90deg,#d9dedf 0%,#c9d0d1 35%,#e9e9e6 60%,#f4f2ee 100%)}
.hero-rule{left:0;width:432px;height:2px;background:var(--green-deep)}
.hero-arabic{left:48px;top:366px;font:500 48px "Noto Naskh Arabic",serif;color:var(--green-deep);direction:rtl}
.hero-dots{left:547px;top:664px;display:flex;gap:13px}
.hero-dots i{width:10px;height:10px;border-radius:50%;background:rgba(255,255,255,.75)}
.hero-dots i.on{background:var(--white);box-shadow:0 0 0 2px rgba(255,255,255,.5)}

/* info bar */
.info-bar{left:0;top:725px;width:1200px;height:106px;display:flex;border-bottom:5px solid var(--grey-band)}
.info-cell{display:flex;flex-direction:column;align-items:center;justify-content:center;border-right:1px solid var(--line);font-size:12px;color:var(--text)}
.info-cell:last-child{border-right:0}
.info-cell strong{font:600 12px "Montserrat",sans-serif;color:var(--ink);margin-top:2px}
.info-cell svg{margin-bottom:10px}

/* sections */
.section-title{width:1200px;left:0;text-align:center;font:700 27px "Montserrat",sans-serif;color:var(--green);text-transform:uppercase}
.welcome-text{left:290px;width:620px;top:956px;text-align:center;font-size:13px;line-height:23px}
.btn{display:flex;align-items:center;justify-content:center;background:var(--green);color:var(--white);font:600 12px "Montserrat",sans-serif;text-transform:uppercase}

/* services wheel */
.svc-label{font:700 15px "Montserrat",sans-serif;color:var(--ink);text-transform:uppercase;display:flex;align-items:center;gap:8px}
.svc-desc{font-size:12px;line-height:21px;width:230px;text-align:center;color:var(--text)}

/* blog */
.blog-band{left:0;top:1815px;width:1200px;height:542px;background:var(--grey-band)}
.post{top:1960px;width:295px;height:397px;background:var(--white)}
.post-photo{width:295px;height:222px}
.post h3{position:absolute;left:30px;top:250px;font:700 12.5px/22px "Montserrat",sans-serif;color:var(--ink);text-transform:uppercase}
.post p{position:absolute;left:30px;top:302px;width:230px;font-size:12px;line-height:22px}
.post .btn{position:absolute;left:30px;top:366px;width:110px;height:31px;font-size:11px}

/* testimonials */
.quote-mark{font:400 90px/1 Georgia,serif;color:#bdbdbd}
.testimonial-text{left:305px;top:2553px;width:590px;text-align:center;font-size:14px;line-height:26px}
.author{left:0;width:1200px;text-align:center}

/* footer */
.site-footer{left:0;top:2823px;width:1200px;height:414px;background:var(--grey-band)}
.footer-badge{left:134px;top:2881px;width:200px;height:200px}
.footer-badge span{font-size:21px}
.col-title{font:700 11px "Montserrat",sans-serif;color:var(--ink);text-transform:uppercase}
.col-list{font-size:12px;line-height:22.6px;color:var(--text);list-style:none}
.email-box{left:807px;top:2933px;width:259px;height:69px;background:var(--white);display:flex;align-items:center;padding-left:24px;gap:16px;font-size:12px;color:var(--muted)}
.footer-rule{left:134px;top:3131px;width:932px;height:1px;background:#d5d5d5}
.social{display:flex;gap:8px;align-items:center}
.social i{width:24px;height:24px;border-radius:50%;background:#9aa7a0;display:block}
</style>
</head>
<body>

<header class="site-header">
  <div class="abs call">
    <div class="call-icon"><svg width="15" height="15" viewBox="0 0 24 24"><path fill="#fff" d="M6.6 10.8a15 15 0 0 0 6.6 6.6l2.2-2.2c.3-.3.7-.4 1-.2 1.1.4 2.3.6 3.6.6.6 0 1 .4 1 1V20c0 .6-.4 1-1 1A17 17 0 0 1 3 4c0-.6.4-1 1-1h3.5c.6 0 1 .4 1 1 0 1.3.2 2.5.6 3.6.1.3 0 .7-.2 1z"/></svg></div>
    <div><small>CALL US</small><strong>(555)014.2290</strong></div>
  </div>
  <div class="abs quote-btn"><svg width="13" height="13" viewBox="0 0 24 24"><path fill="none" stroke="#fff" stroke-width="2" d="M4 20h16M5 16l10-10 3 3-10 10H5z"/></svg>GET A QUOTE</div>
  <nav class="abs main-nav">
    <span class="active">Home</span>
    <span style="margin-left:40px">About us</span>
    <span style="margin-left:48px">Services</span>
    <span style="margin-left:50px">Blog</span>
    <span style="margin-left:48px">Testimonials</span>
    <span style="margin-left:44px">Contact us</span>
  </nav>
</header>

<div class="abs brand-badge header-badge"><span>Harbor Lane Services</span></div>

<section class="abs hero" role="img" aria-label="Photograph of a smiling professional in traditional Gulf attire in a bright office"></section>
<div class="abs hero-rule" style="top:360px"></div>
<div class="abs hero-rule" style="top:457px"></div>
<div class="abs hero-arabic" lang="ar">هاربر لين سرفسس ذ.م.م</div>
<div class="abs hero-dots"><i></i><i class="on"></i><i></i><i></i><i></i></div>

<section class="abs info-bar">
  <div class="info-cell" style="width:304px">
    <svg width="20" height="20" viewBox="0 0 24 24"><path fill="none" stroke="#9bcb3b" stroke-width="2.4" d="M4 15v-3a8 8 0 0 1 16 0v3"/><rect x="3" y="13" width="4" height="7" rx="1" fill="#9bcb3b"/><rect x="17" y="13" width="4" height="7" rx="1" fill="#9bcb3b"/></svg>
    It is a long exit<strong>24/7 SUPPORT</strong>
  </div>
  <div class="info-cell" style="width:309px">
    <svg width="20" height="20" viewBox="0 0 24 24"><path fill="#9bcb3b" d="M6.6 10.8a15 15 0 0 0 6.6 6.6l2.2-2.2c.3-.3.7-.4 1-.2 1.1.4 2.3.6 3.6.6.6 0 1 .4 1 1V20c0 .6-.4 1-1 1A17 17 0 0 1 3 4c0-.6.4-1 1-1h3.5c.6 0 1 .4 1 1 0 1.3.2 2.5.6 3.6.1.3 0 .7-.2 1z"/></svg>
    CALL US<strong>(555)014.2290</strong>
  </div>
  <div class="info-cell" style="width:295px">
    <svg width="20" height="20" viewBox="0 0 24 24"><rect x="3" y="5" width="18" height="14" rx="1" fill="none" stroke="#9bcb3b" stroke-width="2"/><path d="M3 6l9 7 9-7" fill="none" stroke="#9bcb3b" stroke-width="2"/></svg>
    EMAIL US<strong>info@harborlaneservices.com</strong>
  </div>
  <div class="info-cell" style="width:292px">
    <svg width="22" height="22" viewBox="0 0 24 24"><rect x="3" y="5" width="15" height="15" rx="1" fill="none" stroke="#9bcb3b" stroke-width="2"/><path d="M10 15l1-4 9-9 3 3-9 9z" fill="#9bcb3b"/></svg>
    <strong>REQUEST A QUOTE TODAY</strong>
  </div>
</section>

<h2 class="abs section-title" style="top:898px">Welcome to our site</h2>
<p class="abs welcome-text">There are many variations of passages of Lorem Ipsum available, but the majority have suffered alteration in some form, by injected humour, or randomised words which don't look even believable. If you are going to use a passa e of Lorem Ipsum.</p>
<div class="abs btn" style="left:531px;top:1064px;width:138px;height:39px">Read more</div>

<!-- services wheel -->
<svg class="abs" style="left:380px;top:1193px" width="440" height="460" viewBox="0 0 440 460" aria-label="Service areas">
  <circle cx="220" cy="220" r="196" fill="none" stroke="#9bcb3b" stroke-width="26"/>
  <circle cx="220" cy="220" r="75" fill="#0f6b3b"/>
  <g fill="#fff" stroke="#e4e4e4" stroke-width="2">
    <circle cx="121" cy="59" r="58"/>
    <circle cx="365" cy="61" r="58"/>
    <circle cx="32" cy="259" r="58"/>
    <circle cx="425" cy="259" r="58" style="display:none"/>
    <circle cx="220" cy="400" r="58"/>
  </g>
  <!-- govt -->
  <g fill="#9bcb3b">
    <path d="M121 36l24 12H97z"/><rect x="99" y="50" width="44" height="4"/>
    <rect x="103" y="57" width="5" height="20"/><rect x="113" y="57" width="5" height="20"/><rect x="124" y="57" width="5" height="20"/><rect x="134" y="57" width="5" height="20"/>
    <rect x="97" y="79" width="48" height="5"/>
  </g>
  <!-- window -->
  <g fill="#9bcb3b">
    <rect x="358" y="40" width="12" height="12"/><rect x="373" y="40" width="12" height="12"/><rect x="358" y="55" width="12" height="12"/><rect x="373" y="55" width="12" height="12"/>
    <path d="M345 82l10-14h5l-8 14z"/>
  </g>
  <!-- office -->
  <g fill="#9bcb3b">
    <rect x="14" y="240" width="22" height="42"/><rect x="38" y="252" width="16" height="30"/>
    <g fill="#fff"><rect x="18" y="246" width="5" height="5"/><rect x="27" y="246" width="5" height="5"/><rect x="18" y="256" width="5" height="5"/><rect x="27" y="256" width="5" height="5"/><rect x="18" y="266" width="5" height="5"/><rect x="27" y="266" width="5" height="5"/><rect x="42" y="258" width="8" height="4"/><rect x="42" y="267" width="8" height="4"/></g>
  </g>
  <!-- retail -->
  <g fill="#9bcb3b">
    <path d="M194 378h52l4 12h-60z"/>
    <rect x="196" y="392" width="48" height="30"/>
    <g fill="#fff"><rect x="202" y="398" width="14" height="12"/><rect x="222" y="398" width="16" height="24"/></g>
  </g>
</svg>
<!-- carpet circle (right) -->
<svg class="abs" style="left:745px;top:1392px" width="122" height="122" viewBox="0 0 122 122">
  <circle cx="61" cy="61" r="58" fill="#fff" stroke="#e4e4e4" stroke-width="2"/>
  <g fill="#9bcb3b"><rect x="36" y="46" width="34" height="30" rx="4"/><path d="M74 48l14-6v4l-14 6zM74 60h16v4H74zM74 72l14 6v-4l-14-6z"/></g>
</svg>

<div class="abs svc-label" style="right:780px;top:1197px">Govt Agencies <svg width="8" height="10"><path d="M0 0l8 5-8 5z" fill="#222"/></svg></div>
<p class="abs svc-desc" style="left:116px;top:1227px">There are many variations of passages of Lorem Ipsum available, but the majority.</p>
<div class="abs svc-label" style="left:798px;top:1197px"><svg width="8" height="10"><path d="M8 0L0 5l8 5z" fill="#222"/></svg> Window Cleaning</div>
<p class="abs svc-desc" style="left:807px;top:1227px">There are many variations of passages of Lorem Ipsum available, but the majority.</p>
<div class="abs svc-label" style="right:855px;top:1413px">Office <svg width="8" height="10"><path d="M0 0l8 5-8 5z" fill="#222"/></svg></div>
<p class="abs svc-desc" style="left:105px;top:1444px;width:240px;text-align:right">There are many variations of passages of Lorem Ipsum available, but the majority.</p>
<div class="abs svc-label" style="left:859px;top:1413px"><svg width="8" height="10"><path d="M8 0L0 5l8 5z" fill="#222"/></svg> Carpet Cleaning</div>
<p class="abs svc-desc" style="left:872px;top:1444px;width:240px;text-align:left">There are many variations of passages of Lorem Ipsum available, but the majority.</p>
<svg class="abs" style="left:596px;top:1664px" width="10" height="8"><path d="M0 8l5-8 5 8z" fill="#222"/></svg>
<div class="abs svc-label" style="left:0;width:1200px;justify-content:center;top:1680px">Retail</div>
<p class="abs svc-desc" style="left:465px;width:270px;top:1712px">There are many variations of passages of Lorem Ipsum available, but the majority.</p>

<!-- blog -->
<section class="abs blog-band"></section>
<h2 class="abs section-title" style="top:1873px">Latest Blog</h2>
<article class="abs post" style="left:134px">
  <div class="post-photo" role="img" aria-label="Photo of a bright clean kitchen floor" style="background:linear-gradient(160deg,#f1f1ef,#d6d8d7)"></div>
  <h3>Contrary to popular belief<br>lorem ipsum</h3>
  <p>page editors now use Lorem Ipsum as their default model text, and a search</p>
  <div class="btn">Read more</div>
</article>
<article class="abs post" style="left:451px">
  <div class="post-photo" role="img" aria-label="Photo of a freshly mopped tiled floor" style="background:linear-gradient(160deg,#e4e6e6,#b9c4c9)"></div>
  <h3>Contrary to popular belief<br>lorem ipsum</h3>
  <p>page editors now use Lorem Ipsum as their default model text, and a search</p>
  <div class="btn">Read more</div>
</article>
<article class="abs post" style="left:773px">
  <div class="post-photo" role="img" aria-label="Photo of a grey upholstered sofa being vacuumed" style="background:linear-gradient(160deg,#cfcfcd,#8e908f)"></div>
  <h3>Contrary to popular belief<br>lorem ipsum</h3>
  <p>page editors now use Lorem Ipsum as their default model text, and a search</p>
  <div class="btn">Read more</div>
</article>

<!-- testimonials -->
<h2 class="abs section-title" style="top:2454px">Testimonials</h2>
<div class="abs quote-mark" style="left:257px;top:2508px">&ldquo;</div>
<p class="abs testimonial-text">There are many variations of passages of Lorem Ipsum available, but the majority have suffered alteration in some form, by injected humour, or randomised words which don't look even slightly believable. If you are going</p>
<div class="abs quote-mark" style="left:788px;top:2620px">&rdquo;</div>
<div class="abs author heading" style="top:2707px;font-weight:700;font-size:11px;color:var(--ink)">DANIEL MORROW</div>
<div class="abs author" style="top:2729px;font-size:10px;color:var(--muted)">ENGLAND</div>
<svg class="abs" style="left:482px;top:2711px" width="18" height="30"><path d="M15 2L3 15l12 13" fill="none" stroke="#aaa" stroke-width="3"/></svg>
<svg class="abs" style="left:698px;top:2711px" width="18" height="30"><path d="M3 2l12 13L3 28" fill="none" stroke="#aaa" stroke-width="3"/></svg>

<!-- footer -->
<footer class="abs site-footer"></footer>
<div class="abs brand-badge footer-badge"><span>Harbor Lane Services</span></div>

<div class="abs col-title" style="left:427px;top:2888px">Menu</div>
<ul class="abs col-list" style="left:427px;top:2922px">
  <li>Home</li><li>About us</li><li>Services</li><li>Blog</li><li>Testimonials</li><li>Contact us</li>
</ul>
<div class="abs col-title" style="left:593px;top:2888px">Contact us</div>
<ul class="abs col-list" style="left:593px;top:2922px">
  <li>418 Cedar Row</li><li>Riverton, NC 28899</li><li>1.555.014.2290</li><li>info@harborlaneservices.com</li>
</ul>
<div class="abs col-title" style="left:807px;top:2888px">Newsletter signup!</div>
<div class="abs email-box">
  <svg width="14" height="11" viewBox="0 0 24 18"><rect x="1" y="1" width="22" height="16" fill="none" stroke="#666" stroke-width="2"/><path d="M1 2l11 8 11-8" fill="none" stroke="#666" stroke-width="2"/></svg>
  E-mail id
</div>
<div class="abs btn" style="left:952px;top:3023px;width:114px;height:44px;font-size:13px">Signup</div>

<div class="abs footer-rule"></div>
<div class="abs social" style="left:134px;top:3173px">
  <span class="heading" style="font-weight:700;font-size:10px;color:var(--ink);margin-right:6px">FOLLOW US</span>
  <i></i><i></i><i></i>
</div>
<div class="abs" style="right:134px;top:3180px;font-size:10px;color:var(--ink)">Copyrights @ 2017 All Rights Reserved</div>

</body>
</html>
```